COFFEE RALLY // COFFEE PATHWAYS // STEADY COFFEE

website that looks kind of: www.trevandor.com OR PIXELHARBR
I sell coffee to sports teams at a very low price and they make the profit for whatever they are looking to raise money for. This is a tool for them to raise money.
I need help creating not just the website but a catchy name for this project.
Now students don't need to wash cars to raise funds, they have my coffee they can sell to turn it into their own profits.

Target Market(s)

sports teams, schools, churches, fundraisers.

Industry/Entity Type

coffee // fundraiser

Coding

Coded - Design and coding required

Number of Pages Required

1 page

Font styles to use
Serif

Colors
0054AA
0677BA
7BADD7
CADEEF
E8F1F8

Requirements
Must have
• Video of how it works (steps) // Get started button // personalize your coffee bag
Nice to have
• Lumvek.com for example as a name for the website

```html
<!DOCTYPE html>
<html lang="en">
<head>
<meta charset="utf-8">
<title>Meridian Ridge Coffee</title>
<link href="https://fonts.googleapis.com/css2?family=Roboto+Serif:ital,wght@0,400;0,500;0,700;1,500&display=swap" rel="stylesheet">
<style>
  :root {
    --ink: #3c3c3c;
    --body: #6b6b6b;
    --blue: #0054aa;
    --blue-dark: #0a3f91;
    --blue-band-top: #0677ba;
    --blue-band-bottom: #0a3a8a;
    --accent: #e8832a;
    --price: #4a1d0e;
    --footer: #0e2a47;
    --frame: #4a4a4a;
    --tint: #e8f1f8;
    --white: #ffffff;
  }
  * { margin: 0; padding: 0; box-sizing: border-box; }
  html, body { width: 1200px; height: 4332px; overflow: hidden; background: var(--white); }
  body { position: relative; font-family: "Roboto Serif", Georgia, serif; color: var(--ink); }
  .abs { position: absolute; }

  /* header */
  .brand { display: flex; align-items: center; gap: 8px; }
  .brand-mark { width: 22px; height: 22px; border-radius: 50%; background: #7a5a2c; flex: none; }
  .brand-name { font-weight: 700; font-size: 14px; color: #7a5a2c; letter-spacing: .4px; line-height: 1.1; white-space: nowrap; }
  .nav a { position: absolute; top: 42px; font-size: 13px; color: var(--ink); text-decoration: none; letter-spacing: .2px; white-space: nowrap; }
  .nav a.active::after { content: ""; position: absolute; left: 0; right: 0; bottom: -9px; height: 3px; background: var(--accent); }
  .btn { position: absolute; display: flex; align-items: center; justify-content: center; background: var(--blue); color: var(--white); font-weight: 700; font-size: 12px; border-radius: 22px; text-decoration: none; letter-spacing: .2px; white-space: nowrap; }
  .btn-dark { background: var(--blue-dark); }

  /* headings */
  .hero-title { left: 0; width: 1200px; top: 150px; text-align: center; font-size: 34px; font-weight: 700; line-height: 44px; color: var(--ink); }
  .section-title { font-size: 41px; font-weight: 700; line-height: 56px; color: var(--ink); white-space: nowrap; }
  .copy { font-size: 13px; line-height: 30px; color: var(--body); }

  .dots span { display: block; width: 8px; height: 8px; border-radius: 50%; background: #555; margin-bottom: 10px; }
  .dots span.on { background: var(--accent); }

  .oval { position: absolute; width: 328px; height: 236px; border-radius: 50%; border: 7px solid var(--frame); }
  .photo { position: absolute; border-radius: 22px; }

  /* how-it-works video */
  .video { display: flex; align-items: center; justify-content: center; }
  .play { width: 74px; height: 74px; border-radius: 50%; background: rgba(255,255,255,.9); display: flex; align-items: center; justify-content: center; }

  .band { left: 0; top: 3017px; width: 1200px; height: 516px; background: linear-gradient(180deg, var(--blue-band-top), var(--blue-band-bottom)); color: var(--white); text-align: center; }
  .band h2 { position: absolute; top: 108px; width: 100%; font-size: 41px; line-height: 57px; font-weight: 700; }
  .band blockquote { position: absolute; top: 232px; left: 210px; width: 780px; font-style: italic; font-weight: 500; font-size: 19px; line-height: 34px; }
  .band .signer { position: absolute; top: 362px; width: 100%; font-weight: 700; font-size: 21px; }
  .band .signer-org { position: absolute; top: 400px; width: 100%; font-size: 16px; }

  .price-line { font-size: 20px; font-weight: 500; color: var(--price); line-height: 31px; }

  footer { left: 0; top: 4160px; width: 1200px; height: 172px; background: var(--footer); }
  .foot-nav a { position: absolute; top: 56px; color: var(--white); font-weight: 700; font-size: 13px; text-decoration: none; white-space: nowrap; }
  .legal { position: absolute; left: 371px; top: 94px; font-size: 10px; color: #d7dde6; white-space: nowrap; }
  .social span { display: inline-block; width: 20px; height: 20px; background: var(--white); border-radius: 3px; margin-right: 10px; }
  .cards span { display: inline-block; width: 32px; height: 21px; border-radius: 3px; margin-right: 8px; }
</style>
</head>
<body>

<header>
  <div class="abs brand" style="left:146px; top:38px; width:190px;">
    <span class="brand-mark"></span>
    <span class="brand-name">MERIDIAN RIDGE</span>
  </div>
  <nav class="nav">
    <a href="#" class="active" style="left:406px;">HOME</a>
    <a href="#" style="left:474px;">ABOUT</a>
    <a href="#" style="left:548px;">SERVICES</a>
    <a href="#" style="left:642px;">OUR BEANS</a>
    <a href="#" style="left:748px;">PRICING</a>
  </nav>
  <a href="#" class="btn btn-dark" style="left:832px; top:29px; width:88px; height:43px;">LOGIN</a>
  <a href="#personalize" class="btn" style="left:926px; top:29px; width:129px; height:43px;">GET STARTED</a>
</header>

<h1 class="abs hero-title">WE HAVE THE CONFIDENCE IN<br>OUR SKILLSET FROM OUR LONG<br>HISTORY OF PRODUCTION TO<br>GRANT YOU PREMIUM COFFEE.</h1>
<a href="#personalize" class="btn" style="left:534px; top:353px; width:131px; height:42px;">GET STARTED</a>

<div class="abs dots" style="left:1117px; top:398px;">
  <span></span><span class="on"></span><span></span><span></span>
</div>

<div class="oval" role="img" aria-label="Group of athletes from many sports" style="left:-4px; top:450px; background:linear-gradient(135deg,#2c3a2a,#7a4b3a);"></div>
<div class="oval" role="img" aria-label="Roasted coffee beans with a scoop" style="left:343px; top:433px; background:linear-gradient(135deg,#5a3420,#2a1a12);"></div>
<div class="oval" role="img" aria-label="Team celebrating at sunset" style="left:695px; top:432px; background:linear-gradient(135deg,#4f5d8a,#d9a25a);"></div>
<div class="oval" role="img" aria-label="Coffee beans and paper cups" style="left:177px; top:675px; background:linear-gradient(135deg,#4d3222,#b0885a);"></div>
<div class="oval" role="img" aria-label="Basketball player dunking under a cloudy sky" style="left:530px; top:675px; background:linear-gradient(135deg,#7aa5c8,#dfe7ef);"></div>
<div class="oval" role="img" aria-label="Cup of coffee among beans" style="left:880px; top:656px; background:linear-gradient(135deg,#3a2417,#8a6a4a);"></div>

<h2 class="abs section-title" style="left:0; width:1200px; top:1022px; text-align:center;">HOW DO YOU MEASURE<br>THE QUALITY?</h2>
<p class="abs copy" style="left:225px; width:750px; top:1163px; text-align:center;">Our Arabica beans are grown at an altitude of 1600-2100' with a humidity level of 10.5-11.5%. These are prime growing conditions to produce a high level of quality and flavor levels for this type of bean. Using these conditions to grow our beans translates into several different flavor notes and types of arabica bean, that are then naturally dried and stored in eco-friendly ecotact bags to ensure maximum freshness.</p>
<a href="#" class="btn" style="left:534px; top:1316px; width:131px; height:42px;">READ MORE</a>

<div class="photo" role="img" aria-label="Person sitting with a takeaway coffee cup" style="left:8px; top:1426px; width:388px; height:427px; background:linear-gradient(160deg,#8a6a52,#4a3526);"></div>
<div class="photo" role="img" aria-label="Coffee beans and ground coffee on a light surface" style="left:407px; top:1426px; width:388px; height:209px; background:linear-gradient(135deg,#e9e7e3,#6a4a34);"></div>
<div class="photo" role="img" aria-label="Woman enjoying coffee at an outdoor cafe" style="left:407px; top:1645px; width:388px; height:208px; background:linear-gradient(135deg,#b9c3c8,#5a5a55);"></div>
<div class="photo" role="img" aria-label="Coffee poured from a moka pot into a cup outdoors" style="left:803px; top:1426px; width:388px; height:427px; background:linear-gradient(160deg,#4a5a48,#2a2f28);"></div>

<h2 class="abs section-title" style="left:143px; top:1951px;">COFFEE<br>WITH A PURPOSE</h2>
<p class="abs copy" style="left:143px; width:496px; top:2078px;">Meridian Ridge Coffee Co. operates as a large-scale coffee growing and harvesting company located within the community of Valle Alto, Ecuador. For over 100 years, we have been known as the most reliable distributor and brewer of high-quality Arabica beans throughout the South American region, according to our satisfied and consistent customer base! We have the experience and knowledge to support the consistent quality of our product. We can assure you that our coffee will make the perfect fundraising product for friends, family and anyone who would like to support the organization of your choice!</p>
<a href="#" class="btn" style="left:143px; top:2352px; width:131px; height:42px;">READ MORE</a>
<div class="photo" role="img" aria-label="Coffee beans drying on raised beds" style="left:674px; top:1952px; width:381px; height:452px; background:linear-gradient(170deg,#8a8a7a,#7a3a22 40%,#5a2a1a);"></div>

<div class="photo video" role="img" aria-label="How it works video: the fundraising steps, over a glass cup of espresso" style="left:143px; top:2481px; width:383px; height:452px; background:linear-gradient(160deg,#2a1812,#6a2a1a 55%,#3a2418);">
  <span class="play"><svg width="26" height="30" viewBox="0 0 26 30" aria-hidden="true"><path d="M3 2 L24 15 L3 28 Z" fill="#0054aa"/></svg></span>
</div>
<h2 class="abs section-title" style="left:600px; top:2517px;">COFFEE PRICING</h2>
<div class="abs price-line" style="left:600px; top:2597px;">$8.75 per bag (12 oz)<br>Usually sold at $15 per bag</div>
<p class="abs copy" style="left:600px; width:455px; top:2661px;">We sell our coffee at a whole price of $8.75. The usual suggested price for this coffee is $15.00. This is so educational institutions can truly focus on providing this product to their students for fundraising purposes and not have to worry about spiked retail costs. Because of this, our prices are very competitive and virtually unmatched.</p>
<a href="#" class="btn" style="left:600px; top:2844px; width:129px; height:42px;">READ MORE</a>

<section class="abs band">
  <h2>WE ARE WITH YOU EVERY<br>STEP OF THE WAY</h2>
  <blockquote>“If you any questions or concerns, please feel free to reach out to me, Daniel Oreval. My contact information is listed in the beginning of this brochure. We know the recipients of our fine coffee will enjoy it as much as we do!”</blockquote>
  <div class="signer">- Daniel Oreval,</div>
  <div class="signer-org">Meridian Ridge Coffee</div>
</section>

<h2 class="abs section-title" style="left:143px; top:3720px;">OUR BEANS</h2>
<p class="abs copy" style="left:143px; width:458px; top:3793px;">We provide a delectable variety of beans that have various flavor notes which include panela, citrus fruits, red fruits, chocolate (cacao) and nuts. The several types of Arabica bean include tipica,caturra, bourbon and catuai which are presented as green when harvested.</p>
<a href="#" class="btn" style="left:143px; top:3948px; width:131px; height:42px;">READ MORE</a>
<div id="personalize" class="photo" role="img" aria-label="Coffee bag personalized with your team's name, among roasted beans" style="left:674px; top:3635px; width:381px; height:452px; background:linear-gradient(160deg,#6a4028,#3a2216);"></div>

<footer class="abs">
  <div class="abs brand" style="left:146px; top:54px; width:190px;">
    <span class="brand-mark"></span>
    <span class="brand-name">MERIDIAN RIDGE</span>
  </div>
  <nav class="foot-nav">
    <a href="#" style="left:371px;">HOME</a>
    <a href="#" style="left:440px;">ABOUT</a>
    <a href="#" style="left:514px;">SERVICES</a>
    <a href="#" style="left:609px;">OUR BEANS</a>
    <a href="#" style="left:717px;">PRICING</a>
  </nav>
  <div class="legal">© 2021 Meridian Ridge Coffee. All Rights Reserved &nbsp;|&nbsp; Privacy</div>
  <div class="abs social" style="left:860px; top:50px;"><span></span><span></span><span></span></div>
  <div class="abs cards" style="left:862px; top:100px;">
    <span style="background:#d8dde6;"></span><span style="background:#e0a030;"></span><span style="background:#c8ccd2;"></span><span style="background:#5a9ad6;"></span><span style="background:#e8edf3;"></span>
  </div>
</footer>

</body>
</html>
```